TALVORE GROUP OF CLINICS

We need a medical & lab report file. The design should be healthcare related. Our current file design has been used for almost 10 years. We need something more fresh & up-to-date. We have attached the current file design.

Need extra days to review

```html
<!DOCTYPE html>
<html lang="en">
<head>
<meta charset="utf-8">
<title>Talvore Medical Report File</title>
<link rel="stylesheet" href="https://fonts.googleapis.com/css2?family=Montserrat:wght@500;600;700;800&family=Open+Sans:wght@400;600&family=Oswald:wght@500&family=Kaushan+Script&display=swap">
<style>
  :root {
    --navy: #131a7a;
    --sky: #3fa3d8;
    --sky-light: #5ab4e2;
    --red: #e0262b;
    --ink: #3a3a3a;
    --paper: #ffffff;
    --stage: #ececee;
    --rule: #9aa0ad;
  }
  * { margin: 0; padding: 0; box-sizing: border-box; }
  html, body { width: 727px; height: 1200px; overflow: hidden; background: var(--stage); }
  .file-cover {
    position: absolute; left: 0; top: 320px; width: 727px; height: 561px;
    background: var(--paper); box-shadow: 0 6px 18px rgba(0,0,0,.18);
    overflow: hidden; font-family: "Open Sans", sans-serif; color: var(--ink);
  }
  .clinic-heading {
    position: absolute; left: 32px; top: 18px;
    font: 700 18px "Montserrat", sans-serif; color: var(--navy); letter-spacing: .2px;
  }
  .clinic-heading span { color: var(--sky); }
  .clinic-list { position: absolute; left: 0; top: 52px; width: 330px; list-style: none; }
  .clinic {
    position: relative; height: 70px; padding: 2px 0 0 97px;
  }
  .clinic + .clinic::before {
    content: ""; position: absolute; left: 97px; right: 18px; top: -4px;
    border-top: 1px dotted var(--rule);
  }
  .badge {
    position: absolute; left: 32px; top: 6px; width: 48px; height: 48px; border-radius: 50%;
    background: var(--sky); border: 2px solid #fff;
    box-shadow: -3px 2px 0 var(--navy);
    font: 600 24px "Montserrat", sans-serif; color: #fff;
    display: flex; align-items: center; justify-content: center;
  }
  .badge svg { position: absolute; right: -5px; top: -6px; width: 13px; height: 17px; }
  .clinic-name { font: 600 9.5px "Montserrat", sans-serif; color: var(--navy); letter-spacing: .3px; margin-bottom: 3px; }
  .clinic-address, .clinic-contact { font-size: 6.6px; line-height: 8.8px; }
  .clinic-address { margin-bottom: 3px; }
  .clinic-contact b { color: var(--red); font-weight: 600; }
  .clinic-contact b.email { color: var(--navy); }
  .imagery { position: absolute; left: 0; top: 0; }
  .brand { position: absolute; left: 404px; top: 370px; display: flex; align-items: center; gap: 5px; }
  .brand-dot { width: 9px; height: 9px; border-radius: 50%; background: var(--sky); }
  .brand-name { font: 600 7px "Montserrat", sans-serif; color: var(--sky); letter-spacing: .3px; }
  .report-title { position: absolute; left: 403px; top: 398px; font: 800 35px/36px "Montserrat", sans-serif; letter-spacing: .5px; }
  .report-title .line-1 { color: var(--navy); display: block; }
  .report-title .line-2 { color: var(--sky); display: block; }
  .report-sub { position: absolute; left: 404px; top: 474px; font: 400 14px "Open Sans", sans-serif; color: #222; }
  .tagline { position: absolute; left: 630px; top: 468px; text-align: right; line-height: 1; transform: translateX(-50%); }
  .tagline .your { display: block; font: 18px "Kaushan Script", cursive; color: var(--sky); margin-bottom: -6px; padding-left: 28px; }
  .tagline .health { display: block; font: 500 20px "Oswald", sans-serif; color: var(--navy); letter-spacing: -.3px; }
  .tagline .partner { display: block; font: 500 20px "Oswald", sans-serif; color: var(--sky); padding-left: 16px; }
</style>
</head>
<body>
<main class="file-cover">
  <h1 class="clinic-heading">TALVORE <span>GROUP OF CLINICS</span></h1>

  <ol class="clinic-list">
    <li class="clinic">
      <div class="badge">1<svg viewBox="0 0 12 16"><path d="M6 0a6 6 0 0 0-6 6c0 4.5 6 10 6 10s6-5.5 6-10a6 6 0 0 0-6-6z" fill="#e0262b"/><circle cx="6" cy="6" r="2.3" fill="#fff"/></svg></div>
      <p class="clinic-name">PUSAT PERUBATAN TALVORE</p>
      <p class="clinic-address">Level 12, Wisma Orkid, No.8, Jalan Seri Damai,<br>Off Jalan Cempaka Raya, 50450 Kuala Lumpur.</p>
      <p class="clinic-contact"><b>Tel No:</b> +603-2100 4410 &nbsp;<b>Fax No:</b> +603-2100 4411<br><b class="email">Email:</b> klinik.talvore@mailbox.com</p>
    </li>
    <li class="clinic">
      <div class="badge">2<svg viewBox="0 0 12 16"><path d="M6 0a6 6 0 0 0-6 6c0 4.5 6 10 6 10s6-5.5 6-10a6 6 0 0 0-6-6z" fill="#e0262b"/><circle cx="6" cy="6" r="2.3" fill="#fff"/></svg></div>
      <p class="clinic-name">KLINIK TALVORE (BUKIT SERINDIT)</p>
      <p class="clinic-address">No.22, Jalan Cendana B4/2, Bukit Serindit,<br>40460 Shah Alam, Selangor Darul Ehsan.</p>
      <p class="clinic-contact"><b>Tel No:</b> +603-7720 5310 &nbsp;<b>Fax No:</b> +603-7720 5311<br><b class="email">Email:</b> klinik.talvore.bs@mailbox.com</p>
    </li>
    <li class="clinic">
      <div class="badge">3<svg viewBox="0 0 12 16"><path d="M6 0a6 6 0 0 0-6 6c0 4.5 6 10 6 10s6-5.5 6-10a6 6 0 0 0-6-6z" fill="#e0262b"/><circle cx="6" cy="6" r="2.3" fill="#fff"/></svg></div>
      <p class="clinic-name">KLINIK TALVORE (TANJUNG AMAN)</p>
      <p class="clinic-address">Lot 14-1-1, 2A-1-2, 2A-1-3,<br>Persiaran Merbah, Aman Square, 11950 Tanjung Aman, Penang.</p>
      <p class="clinic-contact"><b>Tel No:</b> +604-388 1520 &nbsp;<b>Fax No:</b> +604-388 1521<br><b class="email">Email:</b> klinik.talvore.aman@mailbox.com</p>
    </li>
    <li class="clinic">
      <div class="badge">4<svg viewBox="0 0 12 16"><path d="M6 0a6 6 0 0 0-6 6c0 4.5 6 10 6 10s6-5.5 6-10a6 6 0 0 0-6-6z" fill="#e0262b"/><circle cx="6" cy="6" r="2.3" fill="#fff"/></svg></div>
      <p class="clinic-name">KLINIK TALVORE (SERI BAYU)</p>
      <p class="clinic-address">No. 41, Jalan Niaga Seri Bayu 2/5, Pusat Niaga Seri Bayu<br>Seri Bayu, 71960 Bandar Seri Bayu, Negeri Sembilan.</p>
      <p class="clinic-contact"><b>Tel No:</b> +606-715 2240 &nbsp;<b>Fax No:</b> +606-715 2247<br><b class="email">Email:</b> klinik.talvore.seribayu@mailbox.com</p>
    </li>
    <li class="clinic">
      <div class="badge">5<svg viewBox="0 0 12 16"><path d="M6 0a6 6 0 0 0-6 6c0 4.5 6 10 6 10s6-5.5 6-10a6 6 0 0 0-6-6z" fill="#e0262b"/><circle cx="6" cy="6" r="2.3" fill="#fff"/></svg></div>
      <p class="clinic-name">TALVORE MEDICAL CLINIC (NTA)</p>
      <p class="clinic-address">Lot GATE 07, Arrival Level, Main Terminal Building,<br>NTA, 64100 Sepang, Selangor Darul Ehsan.</p>
      <p class="clinic-contact"><b>Tel No:</b> +603-8640 2209 &nbsp;<b>Fax No:</b> +603-8640 2201<br><b class="email">Email:</b> talvore.nta@mailbox.com</p>
    </li>
    <li class="clinic">
      <div class="badge">6<svg viewBox="0 0 12 16"><path d="M6 0a6 6 0 0 0-6 6c0 4.5 6 10 6 10s6-5.5 6-10a6 6 0 0 0-6-6z" fill="#e0262b"/><circle cx="6" cy="6" r="2.3" fill="#fff"/></svg></div>
      <p class="clinic-name">TALVORE MEDICAL CLINIC [NTA2]</p>
      <p class="clinic-address">S3-1.204, Landside Arrival Level,<br>NTA2, 64100 Sepang, Selangor Darul Ehsan.</p>
      <p class="clinic-contact"><b>Tel No:</b> +603-8642 3309 &nbsp;<b>Fax No:</b> +603-8642 3302<br><b class="email">Email:</b> talvore.nta2@mailbox.com</p>
    </li>
    <li class="clinic">
      <div class="badge">7<svg viewBox="0 0 12 16"><path d="M6 0a6 6 0 0 0-6 6c0 4.5 6 10 6 10s6-5.5 6-10a6 6 0 0 0-6-6z" fill="#e0262b"/><circle cx="6" cy="6" r="2.3" fill="#fff"/></svg></div>
      <p class="clinic-name">TALVORE MEDICAL CLINIC (ITA)</p>
      <p class="clinic-address">2108 Level 1, Passenger Terminal Building,<br>Island International Airport, 11950 Tanjung Aman, Penang.</p>
      <p class="clinic-contact"><b>Tel No:</b> +604-655 3120 &nbsp;<b>Fax No:</b> +604-655 3127<br><b class="email">Email:</b> talvore.clinic@mailbox.com</p>
    </li>
  </ol>

  <svg class="imagery" width="727" height="561" viewBox="0 0 727 561">
    <defs>
      <linearGradient id="labTone" x1="0" y1="0" x2="1" y2="1">
        <stop offset="0" stop-color="#35c6f2"/>
        <stop offset=".55" stop-color="#1c79c9"/>
        <stop offset="1" stop-color="#0c2f7d"/>
      </linearGradient>
      <radialGradient id="scanTone" cx=".5" cy=".45" r=".6">
        <stop offset="0" stop-color="#4aa0f0"/>
        <stop offset="1" stop-color="#0a2a8a"/>
      </radialGradient>
      <radialGradient id="spineTone" cx=".45" cy=".55" r=".6">
        <stop offset="0" stop-color="#e9855a"/>
        <stop offset=".3" stop-color="#3b7ee8"/>
        <stop offset="1" stop-color="#0d3bb0"/>
      </radialGradient>
      <clipPath id="labClip"><circle cx="620" cy="110" r="260"/></clipPath>
    </defs>
    <circle cx="620" cy="110" r="265" fill="none" stroke="#131a7a" stroke-width="1.2"/>
    <rect x="360" y="0" width="367" height="400" fill="url(#labTone)" clip-path="url(#labClip)" role="img" aria-label="Photo of a laboratory scientist in cap and gloves looking into a microscope"/>
    <circle cx="458" cy="272" r="39" fill="url(#scanTone)" stroke="#fff" stroke-width="3" role="img" aria-label="Medical scan illustration of a human skeleton with highlighted spine"/>
    <circle cx="530" cy="318" r="51" fill="url(#scanTone)" stroke="#fff" stroke-width="3" role="img" aria-label="Medical illustration of a human head with glowing brain"/>
    <circle cx="649" cy="338" r="70" fill="url(#spineTone)" stroke="#fff" stroke-width="3" role="img" aria-label="Medical illustration of a spine with highlighted painful vertebra"/>
  </svg>

  <div class="brand"><span class="brand-dot"></span><span class="brand-name">TALVORE GROUP</span></div>
  <h2 class="report-title"><span class="line-1">MEDICAL</span><span class="line-2">REPORT</span></h2>
  <p class="report-sub">Private &amp; Confidential</p>
  <p class="tagline"><span class="your">Your</span><span class="health">Healthcare</span><span class="partner">Partner</span></p>
</main>
</body>
</html>
```